Modern Verdell Tree Care Website

I need a website for a full service Tree Care company. The company provides tree pruning, tree removal, tree preservation, emergency services, stump grinding, and emergency tree services.

Target Market(s)

Customers that need tree services

Industry/Entity Type

Landscaping, Tree Services

Coding

Coded - Design and coding required

Number of Pages Required

5+ page

Font styles to use
Sans Serif

Requirements
Must have
• Good clean design that showcases the services the company provides.
Nice to have
• Services page; contact form, blog, home page, about page

```html
<!DOCTYPE html>
<html lang="en">
<head>
<meta charset="utf-8">
<title>Verdell Tree Care</title>
<link rel="stylesheet" href="https://fonts.googleapis.com/css2?family=Montserrat:wght@300;400;500;600;700;800&display=swap">
<style>
:root{
  --green:#7cc242;
  --green-dark:#3d5e29;
  --orange:#f7a21b;
  --ink:#2b2b2b;
  --muted:#555;
  --icon:#8a8a8a;
  --cream:#f4f6dc;
  --white:#fff;
  --line:#d9d9d9;
}
*{box-sizing:border-box;margin:0;padding:0}
html,body{width:1200px;height:4521px;overflow:hidden}
body{position:relative;font-family:'Montserrat',sans-serif;color:var(--ink);background:var(--white)}
.abs{position:absolute}
.brand{display:flex;align-items:center;gap:12px}
.brand-mark{width:40px;height:40px;background:var(--green)}
.brand-name{font-weight:700;font-size:22px;line-height:1.05;color:var(--ink);letter-spacing:1px;text-transform:uppercase}

/* header */
.site-header{left:0;top:0;width:1200px;height:82px;background:var(--white)}
.site-header .brand{position:absolute;left:86px;top:18px}
.main-nav{position:absolute;left:330px;top:0;height:82px;display:flex;align-items:center;font-size:13px;font-weight:500;letter-spacing:1.5px}
.main-nav a{color:var(--ink);text-decoration:none}
.main-nav a.active{color:var(--green)}
.main-nav .sep{color:#aaa;margin:0 30px}
.header-phone{position:absolute;left:961px;top:0;width:239px;height:82px;background:var(--green);clip-path:polygon(20px 0,100% 0,100% 100%,0 100%);display:flex;align-items:center;gap:10px;padding-left:32px;color:var(--white);font-size:15px;letter-spacing:1.5px;font-weight:500}
.phone-dot{width:24px;height:24px;border-radius:50%;background:var(--white);display:flex;align-items:center;justify-content:center}

/* hero */
.hero{left:0;top:82px;width:1200px;height:680px}
.hero-photo{position:absolute;inset:0;background:linear-gradient(100deg,#7cc242 0%,#6aae38 35%,#4d7e2e 60%,#6b5a3e 80%,#8a8f5c 100%)}
.hero-copy{position:absolute;left:110px;top:150px;color:var(--white)}
.hero-copy h1{font-size:54px;line-height:56px;font-weight:800;letter-spacing:1px}
.hero-copy h1 .light{font-weight:300}
.hero-copy p{margin-top:18px;font-size:17px}
.btn{display:inline-block;background:var(--orange);color:var(--white);font-weight:600;font-size:14px;letter-spacing:1px;text-transform:uppercase;text-align:center;text-decoration:none}
.hero .btn{position:absolute;left:110px;top:383px;width:174px;height:44px;line-height:44px;box-shadow:5px 4px 0 0 #f9c46a}

/* section titles */
.section-title{font-size:35px;font-weight:700;letter-spacing:1px;text-transform:uppercase;text-align:center;width:1200px;left:0}
.section-title .hl{color:var(--green);font-weight:600}

/* services */
.service{width:328px}
.service-photo{width:328px;height:207px;background:linear-gradient(160deg,#9ec36a,#5b7e34 60%,#6a4e32)}
.service-label{display:flex;align-items:center;gap:14px;margin-top:-30px;padding-left:18px}
.service-icon{width:62px;height:62px;border-radius:50%;border:5px solid var(--white);box-shadow:0 2px 6px rgba(0,0,0,.15);display:flex;align-items:center;justify-content:center;flex:none}
.service-icon.g{background:var(--green)}
.service-icon.o{background:var(--orange)}
.service-label h3{font-size:19px;font-weight:700;letter-spacing:.5px;text-transform:uppercase;margin-top:24px;line-height:1.2}

/* who we are */
.who{left:0;top:1490px;width:1200px;height:676px}
.who-photo{position:absolute;inset:0;background:linear-gradient(90deg,#7a7463 0%,#a07a58 18%,#7b6d53 34%,#4c6a36 52%,#3d5e29 70%,#3a5826 100%)}
.who-copy{position:absolute;left:610px;top:198px;width:520px;color:var(--white)}
.who-copy h2{font-size:34px;font-weight:700;letter-spacing:1px}
.who-copy p{font-size:15px;line-height:23px;margin-top:24px}
.who-copy p + p{margin-top:21px}
.who .btn{position:absolute;left:628px;top:520px;width:172px;height:39px;line-height:39px;background:var(--green);box-shadow:5px 4px 0 -1px var(--green-dark),5px 4px 0 1px var(--white)}

/* why choose us */
.why-tree{left:430px;top:2340px;width:350px;height:310px;background:radial-gradient(ellipse at 50% 40%,#5f9a37 0%,#3f7324 55%,transparent 72%)}
.feature{display:flex;align-items:center;gap:14px;font-size:16px;font-weight:700;text-transform:uppercase;line-height:21px}
.feature.left-text{flex-direction:row-reverse;text-align:right}
.f-icon{width:82px;height:82px;border-radius:50%;display:flex;align-items:center;justify-content:center;flex:none}
.f-icon.g{background:var(--green)}
.f-icon.o{background:var(--orange)}

/* blogs */
.blogs{left:0;top:2894px;width:1200px;height:640px;background:var(--cream)}
.blogs h2{position:absolute;left:106px;top:72px;font-size:35px;font-weight:700;letter-spacing:1px}
.blogs h2 .hl{color:var(--green);font-weight:600}
.blog-card{position:absolute;background:var(--white);border:1px solid var(--line)}
.blog-photo{background:linear-gradient(150deg,#a8a59a,#6a6456 50%,#8c7a62)}
.date-tag{background:var(--green);color:var(--white);font-size:11px;font-weight:600;padding:5px 12px;display:inline-block}
.blog-card h3{font-size:18px;font-weight:600;line-height:27px}
.blog-card .more{color:var(--green);font-size:13px;font-weight:600;text-decoration:underline;text-transform:uppercase}
.blog-card.big{left:110px;top:156px;width:474px;height:406px}
.blog-card.big .blog-photo{height:283px}
.blog-card.big .date-tag{position:absolute;left:14px;top:261px}
.blog-card.big .body{padding:22px 38px}
.blog-card.small{width:500px;height:193px;left:605px;display:flex}
.blog-card.small .blog-photo{width:237px;height:100%;flex:none}
.blog-card.small .body{padding:40px 26px 0}
.blog-card.small .date-tag{font-size:10px;padding:4px 12px}
.blog-card.small h3{font-size:14px;line-height:19px;margin:14px 0 10px}
.blog-card.small .more{font-size:11px}

/* contact */
.contact{left:0;top:3480px;width:1200px;height:725px;background:linear-gradient(180deg,#79b93e,#5b9a2c 60%,#6aa934)}
.contact h2{position:absolute;left:0;width:1200px;top:222px;text-align:center;color:var(--white);font-size:35px;font-weight:700;letter-spacing:1px}
.field{position:absolute;background:var(--white);display:flex;align-items:center;gap:10px;padding-left:22px;font-size:13px;color:var(--muted)}
.field.msg{align-items:flex-start;padding-top:20px}
.contact .btn{position:absolute;left:505px;top:591px;width:193px;height:42px;line-height:42px;box-shadow:5px 4px 0 -1px #5b9a2c,5px 4px 0 1px var(--white)}

/* footer */
.site-footer{left:0;top:4205px;width:1200px;height:316px;background:var(--white)}
.site-footer .brand{position:absolute;left:140px;top:78px}
.site-footer .brand-mark{width:56px;height:56px}
.site-footer .brand-name{font-size:28px}
.copyright{position:absolute;left:142px;top:178px;font-size:13px;line-height:22px;color:var(--muted)}
.f-col{position:absolute;top:0;height:316px;border-left:1px solid var(--line);padding-top:74px}
.f-col h4{font-size:16px;font-weight:600;letter-spacing:.5px;text-transform:uppercase;margin-bottom:18px}
.f-col ul{list-style:none;font-size:13px;line-height:29px}
.f-col ul a{color:var(--ink);text-decoration:none}
.f-col ul a.active{text-decoration:underline}
.c-item{display:flex;gap:14px;font-size:13px;line-height:17px;margin-bottom:16px}
.c-item small{font-size:12px;color:var(--muted);display:block}
.c-item b{font-weight:600}
.socials{display:flex;gap:14px}
.social{width:26px;height:26px;border-radius:50%;background:var(--orange)}
</style>
</head>
<body>

<header class="site-header abs">
  <div class="brand"><span class="brand-mark"></span><span class="brand-name">Verdell<br>Tree Care</span></div>
  <nav class="main-nav">
    <a class="active" href="#">HOME</a><span class="sep">|</span>
    <a href="#">ABOUT US</a><span class="sep">|</span>
    <a href="#">SERVICES</a><span class="sep">|</span>
    <a href="#">BLOG</a><span class="sep">|</span>
    <a href="#">CONTACT US</a>
  </nav>
  <div class="header-phone"><span class="phone-dot"><svg width="13" height="13" viewBox="0 0 24 24"><path fill="#7cc242" d="M6.6 10.8a15 15 0 0 0 6.6 6.6l2.2-2.2c.3-.3.7-.4 1-.2 1.1.4 2.3.6 3.6.6.6 0 1 .4 1 1V20c0 .6-.4 1-1 1A17 17 0 0 1 3 4c0-.6.4-1 1-1h3.5c.6 0 1 .4 1 1 0 1.3.2 2.5.6 3.6.1.3 0 .7-.2 1z"/></svg></span>(555) 010 4826</div>
</header>

<section class="hero abs">
  <div class="hero-photo" role="img" aria-label="Arborist in safety gear cutting a large tree trunk with a chainsaw"></div>
  <div class="hero-copy">
    <h1>VERDELL FOR<br>ALL YOUR TREE<br><span class="light">CARE NEEDS</span></h1>
    <p>Serving Marrowfield and surrounding areas.</p>
  </div>
  <a class="btn" href="#">Contact Us</a>
  <svg class="abs" style="left:0;top:0" width="1200" height="680" viewBox="0 0 1200 680">
    <polygon points="0,546 596,654 1200,536 1200,680 0,680" fill="#fff"/>
    <polyline points="0,552 596,662 1200,542" fill="none" stroke="#f7a21b" stroke-width="7"/>
  </svg>
</section>

<h2 class="section-title abs" style="top:818px">Our <span class="hl">Services</span></h2>

<article class="service abs" style="left:86px;top:891px"><div class="service-photo" role="img" aria-label="Pruning shears cutting a branch"></div><div class="service-label"><span class="service-icon g"><svg width="28" height="28" viewBox="0 0 24 24" fill="none" stroke="#fff" stroke-width="1.6"><path d="M4 20 20 4M8 8l8 8"/></svg></span><h3>Tree Pruning</h3></div></article>
<article class="service abs" style="left:431px;top:891px"><div class="service-photo" role="img" aria-label="Chainsaw cutting at the base of a tree"></div><div class="service-label"><span class="service-icon o"><svg width="28" height="28" viewBox="0 0 24 24" fill="none" stroke="#fff" stroke-width="1.6"><rect x="5" y="10" width="14" height="8"/><path d="M12 4v6"/></svg></span><h3>Tree Removal</h3></div></article>
<article class="service abs" style="left:779px;top:891px"><div class="service-photo" role="img" aria-label="Shovel digging soil around a young plant"></div><div class="service-label"><span class="service-icon g"><svg width="28" height="28" viewBox="0 0 24 24" fill="none" stroke="#fff" stroke-width="1.6"><path d="M12 3 4 6v6c0 5 8 9 8 9s8-4 8-9V6z"/></svg></span><h3>Tree Preservation</h3></div></article>
<article class="service abs" style="left:89px;top:1173px"><div class="service-photo" role="img" aria-label="Stump grinder working on a tree stump"></div><div class="service-label"><span class="service-icon g"><svg width="28" height="28" viewBox="0 0 24 24" fill="none" stroke="#fff" stroke-width="1.6"><circle cx="12" cy="12" r="7"/><path d="M12 5v14M5 12h14"/></svg></span><h3>Stump Grinding</h3></div></article>
<article class="service abs" style="left:434px;top:1173px"><div class="service-photo" role="img" aria-label="Fallen tree split after a storm"></div><div class="service-label"><span class="service-icon g"><svg width="28" height="28" viewBox="0 0 24 24" fill="none" stroke="#fff" stroke-width="1.6"><path d="M12 3v18M7 8l5-5 5 5"/></svg></span><h3>Tree Emergency<br>Services</h3></div></article>
<article class="service abs" style="left:782px;top:1173px"><div class="service-photo" role="img" aria-label="Arborist climbing a tree with ropes"></div><div class="service-label"><span class="service-icon g"><svg width="28" height="28" viewBox="0 0 24 24" fill="none" stroke="#fff" stroke-width="1.6"><circle cx="12" cy="9" r="6"/><path d="M12 15v6"/></svg></span><h3>Cabling &amp; Bracing</h3></div></article>

<section class="who abs">
  <div class="who-photo" role="img" aria-label="Arborist in hi-vis shirt and helmet cutting a log with a chainsaw"></div>
  <svg class="abs" style="left:0;top:0" width="1200" height="130" viewBox="0 0 1200 130">
    <polygon points="0,0 1200,0 1200,124 772,13 0,120" fill="#fff"/>
    <polyline points="0,124 772,17 1200,128" fill="none" stroke="#f7a21b" stroke-width="9"/>
  </svg>
  <div class="who-copy">
    <h2>WHO WE ARE</h2>
    <p>At Verdell Tree Care, we are more than just a tree service company, we are stewards of our beautiful trees. With a passion deeply rooted in arboriculture, we embark on a mission to promote the health, beauty, and safety of your trees and landscapes.</p>
    <p>Whether it's expert tree trimming to enhance aesthetics, meticulous tree removal to mitigate hazards, or comprehensive tree health assessments to ensure safety , we approach each task with unwavering dedication and attention to detail.</p>
  </div>
  <a class="btn" href="#">Learn More</a>
</section>

<h2 class="section-title abs" style="top:2250px">Why <span class="hl">Choose Us</span></h2>

<svg class="abs" style="left:340px;top:2340px" width="530" height="410" viewBox="0 0 530 410"><ellipse cx="265" cy="190" rx="248" ry="212" fill="none" stroke="#f9c46a" stroke-width="1.5"/></svg>
<div class="why-tree abs" role="img" aria-label="Large green leafy tree"></div>

<div class="feature left-text abs" style="left:190px;top:2320px"><span class="f-icon g"><svg width="36" height="36" viewBox="0 0 24 24" fill="none" stroke="#fff" stroke-width="1.4"><rect x="5" y="4" width="14" height="16"/><path d="m9 12 2 2 4-4"/></svg></span><span>Licensed and<br>Insured</span></div>
<div class="feature left-text abs" style="left:118px;top:2474px"><span class="f-icon o"><svg width="36" height="36" viewBox="0 0 24 24" fill="none" stroke="#fff" stroke-width="1.4"><circle cx="12" cy="12" r="8"/><path d="M12 7v5l3 2"/></svg></span><span>24 Hour Emergency<br>Services</span></div>
<div class="feature left-text abs" style="left:222px;top:2623px"><span class="f-icon g"><svg width="36" height="36" viewBox="0 0 24 24" fill="none" stroke="#fff" stroke-width="1.4"><path d="M12 21s-6-6-6-11a6 6 0 0 1 12 0c0 5-6 11-6 11z"/><circle cx="12" cy="10" r="2"/></svg></span><span>Locally Owned<br>&amp; Operated</span></div>
<div class="abs" style="left:564px;top:2702px"><span class="f-icon o"><svg width="36" height="36" viewBox="0 0 24 24" fill="none" stroke="#fff" stroke-width="1.4"><circle cx="12" cy="8" r="3"/><path d="M6 20a6 6 0 0 1 12 0"/></svg></span></div>
<div class="abs" style="left:505px;top:2793px;width:200px;text-align:center;font-size:16px;font-weight:700;line-height:21px">LICENSED ARBORIST<br>ON STAFF</div>
<div class="feature abs" style="left:771px;top:2630px"><span class="f-icon g"><svg width="36" height="36" viewBox="0 0 24 24" fill="none" stroke="#fff" stroke-width="1.4"><rect x="5" y="4" width="12" height="16"/><path d="M8 9h6M8 13h6M8 17h4"/></svg></span><span>Free Estimate</span></div>
<div class="feature abs" style="left:827px;top:2478px"><span class="f-icon o"><svg width="36" height="36" viewBox="0 0 24 24" fill="none" stroke="#fff" stroke-width="1.4"><path d="M6 11a6 6 0 0 1 12 0H6z"/><path d="M7 20a5 5 0 0 1 10 0"/></svg></span><span>Safety is our<br>top priority</span></div>
<div class="feature abs" style="left:803px;top:2325px"><span class="f-icon g"><svg width="36" height="36" viewBox="0 0 24 24" fill="none" stroke="#fff" stroke-width="1.4"><circle cx="12" cy="9" r="6"/><path d="M12 15v6M9 21h6"/></svg></span><span>Professional<br>Work</span></div>

<section class="blogs abs">
  <h2>LATEST <span class="hl">BLOGS</span></h2>
  <article class="blog-card big">
    <div class="blog-photo" role="img" aria-label="Chainsaw cutting into a tree trunk with sawdust flying"></div>
    <span class="date-tag">20 MAY 2024</span>
    <div class="body"><h3>Lorem ipsum dolor sit amet consectetur adipiscing elit sed do eiusmod</h3><a class="more" href="#">Learn More</a></div>
  </article>
  <article class="blog-card small" style="top:156px">
    <div class="blog-photo" role="img" aria-label="Arborist climbing a tree trunk"></div>
    <div class="body"><span class="date-tag">20 MAY 2024</span><h3>Lorem ipsum dolor sit amet consectetur adipiscing elit sed do eiusmod</h3><a class="more" href="#">Learn More</a></div>
  </article>
  <article class="blog-card small" style="top:369px">
    <div class="blog-photo" style="background:linear-gradient(150deg,#8fb56a,#4d7a34 55%,#c9c4b0)" role="img" aria-label="Worker trimming branches with long shears"></div>
    <div class="body"><span class="date-tag">10 MAY 2024</span><h3>Lorem ipsum dolor sit amet consectetur adipiscing elit sed do eiusmod</h3><a class="more" href="#">Learn More</a></div>
  </article>
</section>

<section class="contact abs" role="img" aria-label="Soft green forest backdrop">
  <svg class="abs" style="left:0;top:0" width="1200" height="160" viewBox="0 0 1200 160">
    <polygon points="0,0 1200,0 1200,10 465,142 0,28" fill="#f4f6dc"/>
    <polyline points="0,32 465,147 1200,15" fill="none" stroke="#f7a21b" stroke-width="9"/>
  </svg>
  <h2>CONTACT US</h2>
  <div class="field" style="left:210px;top:305px;width:374px;height:56px"><svg width="13" height="13" viewBox="0 0 24 24" fill="#8a8a8a"><circle cx="12" cy="7" r="5"/><path d="M3 22a9 9 0 0 1 18 0z"/></svg>First Name*</div>
  <div class="field" style="left:602px;top:305px;width:375px;height:56px"><svg width="13" height="13" viewBox="0 0 24 24" fill="#8a8a8a"><circle cx="12" cy="7" r="5"/><path d="M3 22a9 9 0 0 1 18 0z"/></svg>Last Name*</div>
  <div class="field" style="left:210px;top:374px;width:374px;height:56px"><svg width="13" height="13" viewBox="0 0 24 24" fill="none" stroke="#8a8a8a" stroke-width="2"><rect x="3" y="6" width="18" height="12"/><path d="m3 6 9 7 9-7"/></svg>Email address</div>
  <div class="field" style="left:602px;top:374px;width:375px;height:56px"><svg width="13" height="13" viewBox="0 0 24 24" fill="#8a8a8a"><path d="M6.6 10.8a15 15 0 0 0 6.6 6.6l2.2-2.2 4.6 1.4V20a1 1 0 0 1-1 1A17 17 0 0 1 3 4a1 1 0 0 1 1-1h3.5l1.4 4.6z"/></svg>Phone number</div>
  <div class="field msg" style="left:210px;top:447px;width:767px;height:119px"><svg width="13" height="13" viewBox="0 0 24 24" fill="#8a8a8a"><path d="M3 4h18v12H9l-5 4v-4H3z"/></svg>Leave Message</div>
  <a class="btn" href="#">Send Message</a>
</section>

<footer class="site-footer abs">
  <div class="brand"><span class="brand-mark"></span><span class="brand-name">Verdell<br>Tree Care</span></div>
  <p class="copyright">Copyright © 2024 Verdell Tree Care<br>All Right Reserved</p>
  <div class="f-col" style="left:435px;width:223px;padding-left:25px">
    <h4>Navigation</h4>
    <ul><li><a class="active" href="#">Home</a></li><li><a href="#">About Us</a></li><li><a href="#">Services</a></li><li><a href="#">Blogs</a></li><li><a href="#">Contact</a></li></ul>
  </div>
  <div class="f-col" style="left:658px;width:279px;padding-left:23px">
    <h4>Contact Us</h4>
    <div class="c-item"><svg width="26" height="26" viewBox="0 0 24 24" fill="none" stroke="#666" stroke-width="1.3"><path d="M6.6 10.8a15 15 0 0 0 6.6 6.6l2.2-2.2 4.6 1.4V20a1 1 0 0 1-1 1A17 17 0 0 1 3 4a1 1 0 0 1 1-1h3.5l1.4 4.6z"/></svg><div><small>Phone number</small><b>(555) 010 4826<br>(555) 017-3051</b></div></div>
    <div class="c-item"><svg width="26" height="26" viewBox="0 0 24 24" fill="none" stroke="#666" stroke-width="1.3"><rect x="3" y="6" width="18" height="12"/><path d="m3 6 9 7 9-7"/></svg><div><small>Email address</small><b>hello@verdelltreecare.com</b></div></div>
  </div>
  <div class="f-col" style="left:937px;width:263px;padding-left:24px">
    <h4>Follow Us</h4>
    <div class="socials"><span class="social" aria-label="Social profile"></span><span class="social" aria-label="Social profile"></span><span class="social" aria-label="Social profile"></span><span class="social" aria-label="Social profile"></span></div>
  </div>
</footer>

</body>
</html>
```